Kraft Eco-friendly pouch back imprint

Updating the design imprint on the back of our eco-friendly kraft stand up pouches. The current package back is a story letter but we want to change it to be more visually eye catching and make better use of buzzwords and graphics. I've uploaded a PDF with the current graphic so that key buzz words and thoughts could be pulled and highlighted.

The printing will be done in black and white, so don't spend time with colors. The imprint area is approximately 7" high x 5" wide.

I definitely want our logo at the top of the package, and I'm attaching two options.

Our mission is to be the Healthiest Pet Bakery in the U.S. That needs to be another point of emphasis.

Other potential buzzwords or bullets include:
Artisan Recipes
Simple Ingredients
No corn, wheat, soy, GMOs, or preservatives
Handcrafted
Locally sourced (Pacific NW)
Eco-conscious company
Updates

The system only allowed 24 hours. That is a ridiculously short time window.

Target Market(s)

Pet parents seeking natural, healthy products

Industry/Entity Type

independent pet channel

Colors

Designer to choose only greyscale colors for use in the design.

Requirements
Must have
• Logo, Mission, buzz words, graphics

```html
<!DOCTYPE html>
<html lang="en">
<head>
<meta charset="utf-8">
<title>Biscuit Lane Bakery – Pouch Back Imprint</title>
<link rel="stylesheet" href="https://fonts.googleapis.com/css2?family=Cabin+Sketch:wght@700&family=Lobster&family=Lobster+Two:ital,wght@1,700&family=Montserrat:wght@700&display=swap">
<style>
  :root {
    --kraft: #c89f6f;
    --kraft-light: #d2ab7c;
    --ink: #2b2220;
    --paper: #efe3d2;
  }
  * { box-sizing: border-box; margin: 0; padding: 0; }
  html, body { width: 1200px; height: 1200px; overflow: hidden; }
  body {
    background: radial-gradient(ellipse at 50% 45%, var(--kraft-light), var(--kraft) 75%);
    color: var(--ink);
    position: relative;
    font-family: "Lobster Two", cursive;
  }
  .abs { position: absolute; }

  /* Brand block */
  .brand-mark {
    left: 525px; top: 78px; width: 150px; height: 150px;
    border-radius: 50%;
    background: radial-gradient(circle at 50% 45%, #5a4438, var(--ink) 70%);
  }
  .brand-name {
    left: 0; width: 1200px; top: 238px;
    text-align: center;
    font-family: "Lobster", cursive;
    font-size: 66px; line-height: 62px;
    color: var(--ink);
  }

  /* Ribbon */
  .ribbon { left: 366px; top: 404px; width: 486px; height: 100px; }
  .ribbon-text {
    left: 406px; top: 409px; width: 396px; height: 68px;
    display: flex; align-items: center; justify-content: center;
    font-family: "Cabin Sketch", cursive; font-weight: 700;
    font-size: 50px; color: var(--paper);
  }

  /* Artisan recipes */
  .artisan {
    left: 0; width: 1200px; top: 492px;
    text-align: center;
    font-family: "Lobster", cursive;
    font-size: 56px; line-height: 54px;
  }
  .artisan .line2 { display: block; padding-left: 40px; }
  .pin-lines { left: 380px; top: 528px; width: 440px; height: 60px; }

  /* Ingredients claim */
  .claim {
    left: 0; width: 1200px; top: 615px;
    text-align: center; font-weight: 700; font-style: italic;
    font-size: 40px; line-height: 56px;
  }
  .claim .region { font-size: 30px; line-height: 40px; font-weight: 700; }

  /* Free-from badges */
  .badges { left: 0; width: 1200px; top: 795px; display: flex; justify-content: center; gap: 20px; }
  .badge {
    width: 98px; height: 98px; border-radius: 50%;
    border: 3px solid var(--ink);
    position: relative; overflow: hidden;
  }
  .badge::before {
    content: ""; position: absolute; inset: 5px; border-radius: 50%;
    border: 1.5px solid var(--ink);
  }
  .badge-slash {
    position: absolute; left: 50%; top: 8px; width: 3px; height: 46px;
    background: var(--ink); transform: translateX(-50%) rotate(45deg);
  }
  .badge-label {
    position: absolute; left: 0; right: 0; bottom: 14px;
    font-family: "Montserrat", sans-serif; font-weight: 700;
    font-size: 11px; line-height: 12px; text-align: center;
  }
  .badge-gmo .badge-label {
    top: 50%; bottom: auto; transform: translateY(-50%);
    font-size: 8px; line-height: 11px;
  }

  /* Mission pill */
  .mission {
    left: 378px; top: 932px; width: 444px; height: 66px;
    background: var(--ink); border-radius: 33px;
  }
  .mission-icon {
    left: 382px; top: 936px; width: 58px; height: 58px;
    border-radius: 50%; background: var(--kraft);
    display: flex; align-items: center; justify-content: center;
  }
  .mission-text {
    left: 445px; top: 938px; width: 370px;
    text-align: center; color: var(--paper);
    font-weight: 700; font-style: italic;
    font-size: 22px; line-height: 28px;
  }

  /* Footer */
  .eco {
    left: 290px; top: 1008px; width: 98px; height: 98px; border-radius: 50%;
    border: 3px solid var(--ink);
    display: flex; align-items: center; justify-content: center;
    font-family: "Montserrat", sans-serif; font-weight: 700; font-size: 10px;
    line-height: 13px; text-align: center;
  }
  .url {
    left: 414px; top: 1022px; width: 390px; text-align: center;
    font-weight: 700; font-style: italic; font-size: 27px;
  }
  .contact {
    left: 414px; top: 1084px; width: 390px;
    display: flex; justify-content: center; gap: 26px;
    font-weight: 700; font-style: italic; font-size: 20px;
  }
  .contact span { display: inline-flex; align-items: center; gap: 6px; }
  .paw {
    left: 818px; top: 1036px; width: 94px; height: 96px;
    border-radius: 46% 46% 50% 50%;
    background: var(--ink);
  }
</style>
</head>
<body>

  <div class="abs brand-mark" role="img" aria-label="Bakery mascot illustration in a round frame"></div>
  <div class="abs brand-name">Biscuit Lane<br>Bakery</div>

  <svg class="abs ribbon" viewBox="0 0 486 100" aria-hidden="true">
    <polygon points="0,90 40,35 40,80 8,96" fill="#2b2220"/>
    <polygon points="486,90 446,35 446,80 478,96" fill="#2b2220"/>
    <polygon points="40,10 446,5 446,72 40,77" fill="#2b2220"/>
    <g stroke="#efe3d2" stroke-width="2">
      <line x1="50" y1="28" x2="70" y2="28"/><line x1="50" y1="40" x2="70" y2="40"/><line x1="50" y1="52" x2="70" y2="52"/>
      <line x1="416" y1="26" x2="436" y2="26"/><line x1="416" y1="38" x2="436" y2="38"/><line x1="416" y1="50" x2="436" y2="50"/>
    </g>
  </svg>
  <div class="abs ribbon-text">Handcrafted</div>

  <svg class="abs pin-lines" viewBox="0 0 440 60" aria-hidden="true">
    <g stroke="#2b2220" stroke-width="4" fill="none" stroke-linecap="round">
      <line x1="0" y1="20" x2="70" y2="20"/>
      <line x1="370" y1="20" x2="440" y2="20"/>
      <line x1="40" y1="40" x2="100" y2="40"/>
      <line x1="345" y1="40" x2="400" y2="40"/>
    </g>
  </svg>
  <div class="abs artisan">Artisan<span class="line2">Recipes</span></div>

  <div class="abs claim">
    Made With Simple,<br>
    – locally sourced ingredients –<br>
    <span class="region">(Pacific NW)</span>
  </div>

  <div class="abs badges">
    <div class="badge"><span class="badge-slash"></span><span class="badge-label">CORN<br>FREE</span></div>
    <div class="badge"><span class="badge-slash"></span><span class="badge-label">WHEAT<br>FREE</span></div>
    <div class="badge"><span class="badge-slash"></span><span class="badge-label">SOY<br>FREE</span></div>
    <div class="badge badge-gmo"><span class="badge-label">GMO FREE<br>NO<br>PRESERVATIVES</span></div>
  </div>

  <div class="abs mission"></div>
  <div class="abs mission-icon">
    <svg width="34" height="30" viewBox="0 0 34 30" aria-hidden="true">
      <path d="M17 28 L3 14 A7 7 0 0 1 17 5 A7 7 0 0 1 31 14 Z" fill="none" stroke="#2b2220" stroke-width="2.5"/>
    </svg>
  </div>
  <div class="abs mission-text">Our mission is to be the Healthiest<br>Pet Bakery in the U.S.</div>

  <div class="abs eco">ECO-<br>CONSCIOUS<br>COMPANY</div>
  <div class="abs url">www.biscuitlanebakery.com</div>
  <div class="abs contact">
    <span>
      <svg width="14" height="20" viewBox="0 0 14 20" aria-hidden="true"><path d="M7 0 A7 7 0 0 1 14 7 C14 12 7 20 7 20 C7 20 0 12 0 7 A7 7 0 0 1 7 0 Z" fill="#2b2220"/><circle cx="7" cy="7" r="2.6" fill="#c89f6f"/></svg>
      Harbor Point, WA
    </span>
    <span>
      <svg width="18" height="18" viewBox="0 0 24 24" aria-hidden="true"><path d="M6.6 10.8a15.1 15.1 0 0 0 6.6 6.6l2.2-2.2a1 1 0 0 1 1-.25 11.4 11.4 0 0 0 3.6.57 1 1 0 0 1 1 1V20a1 1 0 0 1-1 1A17 17 0 0 1 3 4a1 1 0 0 1 1-1h3.5a1 1 0 0 1 1 1c0 1.250.2 2.45.57 3.6a1 1 0 0 1-.25 1z" fill="#2b2220"/></svg>
      555-014-BAKE
    </span>
  </div>
  <div class="abs paw" role="img" aria-label="Paw print graphic"></div>

</body>
</html>
```